Commercial Rooftop Solar business needs a website

We need a website with fantastic appeal for a new company based in Melbourne called Tallow Ridge Energy. We design and install solar energy systems for commercial applications across Australia. Our market is to focus on small to medium businesses looking for solar solutions, but we will also provide our service for residential customers. We would like a beautiful 'front page' feel to our home page, using photographs of solar PV systems and/or natural imagery. Our logo uses the colours orange and black, which could easily be echoed in photographic imagery of sunset and sunrise, for example. The design should communicate quiet confidence and professionalism to a corporate marketplace.

NEW POINTS FOR BRIEF: This design also needs to be flexible to allow for additional future content, including a Support page with sub pages, FAQ's, and a Blog.

As part of this design project, we will require the coding for the website to be completed by the designer.

We have seen some websites, which we like the look and feel of: these are listed below.

brightvanepower.com.au:

• Beautiful images underlaying brief text selling points.
• Simple ‘front cover’ style home page with elegant drop-down menu, stylish simple font style.
• Home page invites exploration through the menu links, rather than trying to provide all the information up front.
• Company logo and name in the top left hand corner, contact details accessible at top right hand, seems consistent in most sites.

kelpworks.com.au

rumbofield.com:
• Same element as the others is the front-page style home page with beautiful images underlying text.

We have a webpage that we started uploading content to. You can use some of the content there in your designs: www.tallowridgeenergy.com.au

Technical Specifications:
PAGES:

Home

About Us

Solutions - Commercial
- Residential

Products - Solar Panels - Vorla Heron, Vorla TELD, Vorla QB
- Solar Inverters - Kestamo, BrilQuill
- Monitoring systems - Dunmere Metrics
- Batteries - RW

- Datasheets have been provided for reference but if it's too much work, you can use generic text and we will provide content later.

Contact Us

FUTURE PAGES (Please consider in structure, where links could be placed):

Support

FAQ's

Blog.

We could provide some content for the Support page soon, but the Blog and FAQ's are future pages which we don't want highlighted in the design as we don't yet have content.

Phone: 1800 7 BIRCH
Email: sales@tallowridgeenergy.com.au

Currently, I do not have images and text available. Please
use placeholders in the meantime. The final text and images will be uploaded for the winner once a winning design has been selected.

Target Market(s)

Primary focus is on small to medium sized business owners. Those owners will have a house which may be suitable for solar so we want to cater to residential deeper in the website.

Industry/Entity Type

Solar Energy

Coding

Coded - Design and coding required

Number of Pages Required

5+ page

Colors
f78f20
0255a3

Requirements
Must have
• Logo as per attachments.
Nice to have
• Logo can have alternate colours Eg. White on Orange or Black etc. provided colour correct logo is shown somewhere eg. footer or contact page.
• In the active site, I'd like to have:
• Very slowly zooming images - barely perceptible.
• Title text that rolls into place
• Subtle movements
• See https://plumtally.com.au/ for example

```html
<!DOCTYPE html>
<html lang="en">
<head>
<meta charset="utf-8">
<title>Tallow Ridge Energy – Commercial Solar Specialists</title>
<link href="https://fonts.googleapis.com/css2?family=Michroma&family=Open+Sans:wght@400;600;700&display=swap" rel="stylesheet">
<style>
:root{
  --orange:#e8521f;
  --black:#101010;
  --footer:#1b1b1b;
  --footer-base:#111;
  --ink:#333;
  --line:#d6d6d6;
  --white:#fff;
}
*{box-sizing:border-box;margin:0;padding:0}
html,body{width:1200px;height:3279px;overflow:hidden}
body{position:relative;font-family:"Open Sans",Arial,sans-serif;color:var(--ink);background:var(--white)}
.abs{position:absolute}
.display{font-family:"Michroma","Arial Black",sans-serif}

/* hero */
.hero{left:0;top:0;width:1200px;height:552px;background:linear-gradient(180deg,#2b2620 0%,#5a4530 35%,#b07a3c 62%,#3b3026 85%,#1f1c1a 100%)}
.hero-photo{left:0;top:0;width:1200px;height:552px}
.brand{left:160px;top:58px;color:var(--white);font-weight:700;font-size:20px;letter-spacing:2px;line-height:1.2}
.topbar{right:152px;top:18px;display:flex;align-items:center;gap:20px;color:var(--white);font-weight:700;font-size:16px}
.topbar .phone{display:flex;align-items:center;gap:8px}
.quote-btn{background:var(--orange);color:var(--white);border:2px solid #ff8a5e;border-radius:18px;padding:5px 14px;font-size:13px;letter-spacing:.5px}
.nav{right:150px;top:84px;display:flex;gap:22px;font-family:"Michroma",sans-serif;font-size:10.5px;letter-spacing:1.2px;color:var(--white)}
.nav .active{color:var(--orange)}
.hero-title{left:0;width:1200px;top:318px;text-align:center;color:var(--white);font-size:25px;letter-spacing:6px;font-weight:400}
.hero-sub{left:0;width:1200px;top:364px;text-align:center;color:var(--white);font-size:18px;letter-spacing:1.5px}
.arrow{top:338px}

/* service band */
.service{top:552px;height:152px;width:600px;display:flex;align-items:center;padding-left:162px;gap:22px;color:var(--white)}
.service.commercial{left:0;background:var(--black)}
.service.residential{left:600px;background:var(--orange);padding-left:30px}
.service-icon{width:102px;height:102px;border-radius:50%;border:4px solid var(--white);display:flex;align-items:center;justify-content:center;flex:none}
.commercial .service-icon{background:var(--orange)}
.residential .service-icon{background:var(--black)}
.service h3{font-family:"Michroma",sans-serif;font-size:14px;font-weight:400;letter-spacing:2px;margin-bottom:8px;white-space:nowrap}
.service p{font-size:12px;line-height:1.55;width:310px}

/* section headings */
.heading{left:0;width:1200px;text-align:center;font-family:"Michroma",sans-serif;font-weight:400;color:var(--black);font-size:24px;letter-spacing:3px;display:flex;justify-content:center;align-items:center;gap:16px}
.heading::before,.heading::after{content:"";width:72px;height:2px;background:var(--black)}
.heading-dot{left:594px;width:12px;height:12px;border-radius:50%;background:#777}

.about-copy{left:168px;width:864px;top:828px;text-align:center;font-size:12.5px;line-height:1.9;color:#444}
.pill{background:var(--orange);color:var(--white);border-radius:18px;font-family:"Michroma",sans-serif;font-size:11px;letter-spacing:1.5px;display:flex;align-items:center;justify-content:center;gap:10px}

/* why choose */
.why{left:0;top:1064px;width:1200px;height:570px;background:linear-gradient(135deg,#f6f7f9 0%,#e4e8ee 50%,#f3f4f6 100%)}
.feature-label{font-size:15px;color:#444;line-height:1.4}
.feature-label.left{text-align:right;width:180px}
.feature-icon{width:74px;height:74px;border-radius:50%;background:var(--orange);border:3px solid #fff;box-shadow:0 0 0 2px var(--orange);display:flex;align-items:center;justify-content:center}
.core-name{left:540px;width:120px;top:1355px;text-align:center;font-weight:700;font-size:13px;line-height:1.35;color:var(--white);letter-spacing:1px}

/* reviews */
.review-lead{left:170px;width:860px;top:1758px;text-align:center;font-weight:700;font-size:15px;line-height:1.75;color:#222}
.avatar{width:96px;height:96px;border-radius:50%;border:3px solid #888;background:linear-gradient(160deg,#9a9ea4,#4a4e55)}
.avatar.active{border-color:var(--orange);background:linear-gradient(160deg,#d8dfe3,#8fa2ad)}
.reviewer{width:160px;text-align:center;font-size:12px;font-weight:600;color:#333}
.reviewer.active{color:var(--orange)}
.review-box{left:162px;top:2015px;width:887px;height:116px;border:1px solid var(--line);padding:24px 30px;font-size:11.5px;line-height:1.75;color:#555;text-align:justify}

/* form */
.form-intro{left:0;width:1200px;top:2302px;text-align:center;font-size:13.5px;color:#333}
.scene{left:0;top:2500px;width:1200px;height:510px;background:linear-gradient(180deg,rgba(255,255,255,0) 0%,#eef1f4 55%,#e4e8ec 100%)}
.field-label{font-size:11.5px;color:#333}
.field{border:1px solid #c9c9c9;background:var(--white);height:36px}
.select{display:flex;align-items:center;justify-content:space-between;padding:0 12px;font-size:12px;color:#333}

/* footer */
.footer{left:0;top:3010px;width:1200px;height:235px;background:var(--footer);color:#ddd}
.footer h4{font-family:"Michroma",sans-serif;font-weight:400;font-size:12px;letter-spacing:2px;color:var(--white)}
.quick-links{list-style:none;font-size:11.5px;line-height:26px;color:#ccc}
.quick-links li{padding-left:12px;border-left:1px solid #555}
.mini-field{background:var(--white);height:20px;font-size:10px;color:#444;padding:3px 8px}
.contact-line{display:flex;align-items:center;gap:10px;font-size:12px;color:#ddd}
.copyright{left:0;top:3245px;width:1200px;height:34px;background:var(--footer-base);color:#bbb;font-size:11px;display:flex;align-items:center;justify-content:center}
</style>
</head>
<body>

<!-- HERO -->
<section class="hero abs">
  <div class="hero-photo abs" role="img" aria-label="City skyline with tall towers at sunset, lit in warm orange light"></div>
  <div class="brand abs">TALLOW RIDGE<br>ENERGY</div>
  <div class="topbar abs">
    <span class="phone">
      <svg width="22" height="22" viewBox="0 0 24 24"><circle cx="12" cy="12" r="11" fill="none" stroke="#fff" stroke-width="2"/><path d="M8.5 6.5l2 2-1.2 1.5a7 7 0 0 0 4.7 4.7l1.5-1.2 2 2-1.3 1.6c-4.5-.4-8.6-4.5-9-9z" fill="#fff"/></svg>
      1800 7 BIRCH
    </span>
    <span class="quote-btn">FREE QUOTE</span>
  </div>
  <nav class="nav abs">
    <span class="active">HOME</span><span>ABOUT US</span><span>COMMERCIAL</span><span>RESIDENTIAL</span><span>PRODUCTS</span><span>CONTACT</span>
  </nav>
  <h1 class="hero-title abs display">TALLOW RIDGE ENERGY</h1>
  <p class="hero-sub abs">COMMERCIAL SOLAR SPECIALISTS</p>
  <svg class="arrow abs" style="left:52px" width="20" height="40" viewBox="0 0 20 40"><path d="M17 2L3 20l14 18" fill="none" stroke="#fff" stroke-width="2.5"/></svg>
  <svg class="arrow abs" style="left:1128px" width="20" height="40" viewBox="0 0 20 40"><path d="M3 2l14 18L3 38" fill="none" stroke="#fff" stroke-width="2.5"/></svg>
</section>

<!-- SERVICES -->
<div class="service commercial abs">
  <div class="service-icon">
    <svg width="44" height="44" viewBox="0 0 44 44" fill="#fff"><rect x="6" y="14" width="14" height="26"/><rect x="22" y="6" width="16" height="34"/><g fill="#e8521f"><rect x="9" y="18" width="3" height="3"/><rect x="14" y="18" width="3" height="3"/><rect x="9" y="25" width="3" height="3"/><rect x="14" y="25" width="3" height="3"/><rect x="25" y="10" width="3" height="3"/><rect x="31" y="10" width="3" height="3"/><rect x="25" y="17" width="3" height="3"/><rect x="31" y="17" width="3" height="3"/><rect x="25" y="24" width="3" height="3"/><rect x="31" y="24" width="3" height="3"/></g></svg>
  </div>
  <div>
    <h3>COMMERCIAL SERVICES</h3>
    <p>The sun shines during the day. You business operates during the day. Isn't solar the perfect match for your business? Let us show you how to slash your energy costs.</p>
  </div>
</div>
<div class="service residential abs">
  <div class="service-icon">
    <svg width="44" height="44" viewBox="0 0 44 44" fill="#fff"><path d="M22 6L4 22h5v16h26V22h5z"/><rect x="18" y="26" width="8" height="12" fill="#101010"/></svg>
  </div>
  <div>
    <h3>RESIDENTIAL SERVICES</h3>
    <p>Home energy costs keep rising. You can put a stop to it now. Find out how we can help.</p>
  </div>
</div>

<!-- ABOUT -->
<h2 class="heading abs" style="top:754px">ABOUT US</h2>
<span class="heading-dot abs" style="top:796px"></span>
<div class="about-copy abs">
  <p>Tallow Ridge Energy is a national company that specialises in solar solutions for the commercial market. We also provide solutions for the residential market, bringing our uncompromising quality and service to the home.</p>
  <p>The founder of the company has over 10 years experience delivering projects on both a residential and commercial scale, having overseen the installation of more than 3 megawatts of solar projects. They were a pioneer on the first megawatt scale project in Australia.As a leader in the field, we offer cutting edge solar technology backed by industry leading warranties. All our systems are designed and installed by Clear Grid Council accredited persons. Our award winning designer will ensure your system will give the best long term performance and return on investment.</p>
</div>
<div class="pill abs" style="left:536px;top:988px;width:138px;height:34px">READ MORE
  <svg width="16" height="16" viewBox="0 0 16 16"><circle cx="8" cy="8" r="8" fill="#fff"/><path d="M6 4l4 4-4 4" fill="none" stroke="#e8521f" stroke-width="2"/></svg>
</div>

<!-- WHY CHOOSE -->
<section class="why abs" role="img" aria-label="Faint background photo of solar panels"></section>
<h2 class="heading abs" style="top:1112px">WHY CHOOSE TALLOW RIDGE</h2>
<span class="heading-dot abs" style="top:1152px"></span>

<svg class="abs" style="left:0;top:1064px" width="1200" height="570" viewBox="0 1064 1200 570">
  <circle cx="600" cy="1373" r="153" fill="none" stroke="#666" stroke-width="1.2"/>
  <circle cx="600" cy="1373" r="68" fill="#2a2a2a"/>
  <g fill="none" stroke="#555" stroke-width="1.2" stroke-dasharray="3 4">
    <path d="M424 1242 L470 1242 L500 1290"/>
    <path d="M424 1390 L447 1390"/>
    <path d="M424 1532 L470 1532 L500 1497"/>
    <path d="M772 1242 L728 1242 L698 1290"/>
    <path d="M772 1390 L753 1390"/>
    <path d="M772 1532 L728 1532 L698 1497"/>
  </g>
  <g fill="#1f3b5b">
    <circle cx="500" cy="1290" r="5"/><circle cx="447" cy="1390" r="5"/><circle cx="500" cy="1497" r="5"/>
    <circle cx="698" cy="1290" r="5"/><circle cx="753" cy="1390" r="5"/><circle cx="698" cy="1497" r="5"/>
  </g>
</svg>
<div class="core-name abs">TALLOW<br>RIDGE</div>

<div class="feature-label left abs" style="left:158px;top:1226px">Comprehensive<br>Monitoring</div>
<div class="feature-icon abs" style="left:350px;top:1205px"><svg width="34" height="30" viewBox="0 0 34 30" fill="none" stroke="#fff" stroke-width="2.2"><rect x="2" y="2" width="30" height="20"/><path d="M6 14h6l3-6 4 10 3-4h6M12 28h10M17 22v6"/></svg></div>

<div class="feature-label left abs" style="left:158px;top:1374px">Performance<br>Guaranteed</div>
<div class="feature-icon abs" style="left:350px;top:1353px"><svg width="30" height="34" viewBox="0 0 30 34" fill="none" stroke="#fff" stroke-width="2.4"><circle cx="15" cy="13" r="10"/><circle cx="15" cy="13" r="4"/><path d="M9 22l-3 10 9-4 9 4-3-10"/></svg></div>

<div class="feature-label left abs" style="left:158px;top:1516px">Top Quality<br>Components</div>
<div class="feature-icon abs" style="left:350px;top:1495px"><svg width="34" height="34" viewBox="0 0 34 34" fill="#fff"><circle cx="17" cy="10" r="7"/><path d="M5 30a12 10 0 0 1 24 0z"/></svg></div>

<div class="feature-icon abs" style="left:772px;top:1205px"><svg width="32" height="32" viewBox="0 0 32 32" fill="none" stroke="#fff" stroke-width="3" stroke-linecap="round"><path d="M6 26L22 10M20 6a6 6 0 0 0 6 6M6 6l20 20"/></svg></div>
<div class="feature-label abs" style="left:866px;top:1226px">Maintenance<br>Included</div>

<div class="feature-icon abs" style="left:772px;top:1353px"><svg width="34" height="34" viewBox="0 0 34 34" fill="#fff"><circle cx="17" cy="12" r="6"/><path d="M6 30a11 9 0 0 1 22 0z"/><circle cx="17" cy="17" r="15" fill="none" stroke="#fff" stroke-width="2"/></svg></div>
<div class="feature-label abs" style="left:866px;top:1374px">Experienced<br>Installers</div>

<div class="feature-icon abs" style="left:772px;top:1495px"><svg width="34" height="34" viewBox="0 0 34 34" fill="none" stroke="#fff" stroke-width="2.4"><circle cx="17" cy="17" r="12"/><path d="M17 10v7l5 4"/></svg></div>
<div class="feature-label abs" style="left:866px;top:1516px">10 Year System<br>Warranty</div>

<!-- REVIEWS -->
<h2 class="heading abs" style="top:1685px">CLIENT REVIEWS</h2>
<span class="heading-dot abs" style="top:1724px"></span>
<p class="review-lead abs">Lorem ipsum dolor sit amet, consectetuer adipiscing elit, sed diam nonummy nibh euismod tincidunt ut laoreet dolore magna aliquam erat volutpat. Ut wisi enim ad minim veniam, quis nostrud exerci tation</p>

<svg class="abs" style="left:234px;top:1892px" width="14" height="24" viewBox="0 0 14 24"><path d="M12 2L2 12l10 10" fill="none" stroke="#bbb" stroke-width="2"/></svg>
<svg class="abs" style="left:952px;top:1892px" width="14" height="24" viewBox="0 0 14 24"><path d="M2 2l10 10L2 22" fill="none" stroke="#bbb" stroke-width="2"/></svg>

<div class="avatar active abs" style="left:286px;top:1856px" role="img" aria-label="Client portrait"></div>
<div class="avatar abs" style="left:470px;top:1856px" role="img" aria-label="Client portrait"></div>
<div class="avatar abs" style="left:644px;top:1856px" role="img" aria-label="Client portrait"></div>
<div class="avatar abs" style="left:826px;top:1856px" role="img" aria-label="Client portrait"></div>
<div class="reviewer active abs" style="left:254px;top:1967px">Mr. Aldo Pressk</div>
<div class="reviewer abs" style="left:438px;top:1967px">Mrs. Wren Talby</div>
<div class="reviewer abs" style="left:612px;top:1967px">Mr. Corin Malvey</div>
<div class="reviewer abs" style="left:794px;top:1967px">Miss Ivy Dorrant</div>

<svg class="abs" style="left:324px;top:2003px" width="28" height="14" viewBox="0 0 28 14"><path d="M0 14L14 0l14 14" fill="#fff" stroke="#d6d6d6"/></svg>
<div class="review-box abs">
  <svg class="abs" style="left:62px;top:24px" width="26" height="18" viewBox="0 0 26 18" fill="#cfcfcf"><path d="M0 18V10C0 4 3 1 9 0v4c-3 1-4 3-4 6h4v8zM15 18V10c0-6 3-9 9-10v4c-3 1-4 3-4 6h4v8z"/></svg>
  &emsp;&emsp;&emsp;&emsp;&emsp;&emsp;Lorem ipsum dolor sitamet, consectetuer adipiscing sed diam nonummy nibh euismod tincidunt ut laoreet dolore magna aliqua volutpat. Ut wisi enim ad minim veniam, quis nostrud exerci tation ullamcorper suscipit lobortis nisl ut aliquip ex ea commodo consequat. Duis autem vel eum iriure dolor in hendrerit in vulputate velit esse molestie consequat.ud exerci tation ullamcorper suscipit lobortis nisl ut commodo.
</div>

<!-- QUOTE FORM -->
<div class="scene abs" role="img" aria-label="Light illustration of wind turbine, solar-roofed house and trees on the left and a factory with rooftop panels and a car on the right"></div>
<h2 class="heading abs" style="top:2226px">YOUR SOLAR SAVINGS START HERE!</h2>
<span class="heading-dot abs" style="top:2264px"></span>
<p class="form-intro abs">We want to help you reduce or eliminate your utility bill and make Massachusetts a cleaner place to live, work, and enjoy life.</p>

<form class="quote-form">
  <label class="field-label abs" style="left:365px;top:2348px">First / Contact Name *</label>
  <div class="field abs" style="left:365px;top:2368px;width:228px"></div>
  <label class="field-label abs" style="left:607px;top:2348px">Last / Company Name *</label>
  <div class="field abs" style="left:607px;top:2368px;width:228px"></div>

  <label class="field-label abs" style="left:365px;top:2418px">Email Address *</label>
  <div class="field abs" style="left:365px;top:2438px;width:470px"></div>

  <label class="field-label abs" style="left:365px;top:2488px">Phone Number *</label>
  <div class="field abs" style="left:365px;top:2508px;width:470px"></div>

  <label class="field-label abs" style="left:365px;top:2560px">Street Address *</label>
  <div class="field abs" style="left:365px;top:2580px;width:470px"></div>

  <label class="field-label abs" style="left:365px;top:2637px">Town / Suburb *</label>
  <div class="field abs" style="left:365px;top:2657px;width:274px"></div>
  <label class="field-label abs" style="left:649px;top:2637px">State *</label>
  <div class="field select abs" style="left:649px;top:2657px;width:96px">VIC
    <svg width="10" height="6" viewBox="0 0 10 6"><path d="M1 1l4 4 4-4" fill="none" stroke="#555" stroke-width="1.5"/></svg></div>
  <label class="field-label abs" style="left:755px;top:2637px">Postcode *</label>
  <div class="field abs" style="left:755px;top:2657px;width:80px"></div>

  <label class="field-label abs" style="left:365px;top:2711px">I am interested in *</label>
  <div class="field select abs" style="left:365px;top:2731px;width:470px">Commercial Solar
    <svg width="12" height="7" viewBox="0 0 12 7"><path d="M1 1l5 5 5-5" fill="none" stroke="#555" stroke-width="1.5"/></svg></div>

  <label class="field-label abs" style="left:365px;top:2790px">Your message</label>
  <div class="field abs" style="left:365px;top:2810px;width:470px;height:86px"></div>

  <div class="pill abs" style="left:555px;top:2920px;width:90px;height:30px">SUBMIT</div>
</form>

<!-- FOOTER -->
<footer class="footer abs">
  <h4 class="abs" style="left:166px;top:30px">QUICK LINKS</h4>
  <ul class="quick-links abs" style="left:166px;top:62px">
    <li>Home</li><li>About Us</li><li>Commercial</li><li>Residential</li><li>Products</li><li>Contact Us</li>
  </ul>

  <h4 class="abs" style="left:366px;top:30px">QUICK INQUIRY</h4>
  <div class="mini-field abs" style="left:366px;top:66px;width:192px">Name</div>
  <div class="mini-field abs" style="left:366px;top:92px;width:192px">Email</div>
  <div class="mini-field abs" style="left:366px;top:118px;width:192px;height:64px">Message</div>
  <div class="pill abs" style="left:366px;top:190px;width:70px;height:22px;font-size:9px">SUBMIT</div>

  <h4 class="abs" style="left:612px;top:30px">CONTACT DETAILS</h4>
  <div class="contact-line abs" style="left:612px;top:70px">
    <svg width="12" height="12" viewBox="0 0 24 24"><path d="M5 2l5 5-2.5 3a12 12 0 0 0 6.5 6.5l3-2.5 5 5-3 3C10 21 3 14 2 5z" fill="#e8521f"/></svg>1800 7 BIRCH</div>
  <div class="contact-line abs" style="left:612px;top:104px">
    <svg width="12" height="10" viewBox="0 0 24 18"><rect width="24" height="18" rx="2" fill="#e8521f"/><path d="M1 2l11 8 11-8" fill="none" stroke="#1b1b1b" stroke-width="2"/></svg>enquiries@tallowridgeenergy.com.au</div>
  <div class="contact-line abs" style="left:612px;top:138px">
    <svg width="12" height="12" viewBox="0 0 24 24"><circle cx="12" cy="12" r="10" fill="none" stroke="#e8521f" stroke-width="3"/><path d="M2 12h20M12 2v20" stroke="#e8521f" stroke-width="2"/></svg>www.tallowridgeenergy.com.au</div>
  <div class="contact-line abs" style="left:612px;top:174px;align-items:flex-start">
    <svg width="12" height="16" viewBox="0 0 24 32"><path d="M12 0a12 12 0 0 0-12 12c0 9 12 20 12 20s12-11 12-20A12 12 0 0 0 12 0z" fill="#e8521f"/><circle cx="12" cy="12" r="4" fill="#1b1b1b"/></svg>
    <span><strong style="color:#fff">TALLOW RIDGE ENERGY</strong><br>Fernlow Park, VIC</span></div>

  <div class="abs" style="left:855px;top:28px;width:1px;height:180px;background:#444"></div>
  <div class="abs" style="left:880px;top:110px;width:200px;text-align:center;color:#fff;font-weight:700;font-size:18px;letter-spacing:1.5px;line-height:1.3">TALLOW RIDGE<br>ENERGY</div>
  <div class="abs" style="left:880px;top:192px;width:200px;text-align:center;font-size:11.5px;color:#ccc">ABN: 41 507 318 624</div>
</footer>
<div class="copyright abs">Copyright © 2017 Tallow Ridge Energy. All Right Reserved.</div>

</body>
</html>
```